Ad design for magazines to promote our Cloud Computing Consulting Company Branding

We need an advertisement design to promote our brand online and on printed magazines (full page). We are a cloud consulting company (products & services on the Cloud) and would like to create an ad that conveys confidence in our services.
Some of the ideas we would want to project are:
First Spanish consulting company specialized in Cloud Computing Technology and Services
We help you incorporate into your business the best Cloud Computing Solutions on the market to improve efficiency, reduce costs and increase competitiveness
Experts in:
• Cloud infrastructure modernization
• Digital Transformation, productivity and collaboration
• Cloud data management
• Advanced analytics
• Cloud application development
• Location Strategy
We are Norvane Sky Ally Prime and have recently achieved a Task Renewal Mastery award
We are also partners of other leading technologies
We have a web page to be used as reference even though we are open to designs that differ from this style. www.brevoltaconsult.example
Target Market(s)
B2B Market Business to Business
Requirements
Must have
- Dimensions: 21x29.7 cm. (width by height) CMYK, 300 dpi, 3 millimeters of bleed and cut lines
Nice to have
- We would like an attractive image with not a lot of text (just about what is on the explanation), including the Ally Prime and Task Renewal badges.

```html
<!DOCTYPE html>
<html lang="en">
<head>
<meta charset="utf-8">
<title>Brevolta Partner — Magazine Ad</title>
<link href="https://fonts.googleapis.com/css2?family=Montserrat:wght@300;400;500;600;700;800&display=swap" rel="stylesheet">
<style>
:root{
  --navy:#0e1533;
  --navy-deep:#0a0f26;
  --plum:#3a1240;
  --cyan:#2fd3c9;
  --red:#e4222b;
  --white:#ffffff;
  --page:#ffffff;
}
*{margin:0;padding:0;box-sizing:border-box}
html,body{width:1200px;height:2591px;overflow:hidden;background:var(--page)}
body{position:relative;font-family:'Montserrat',sans-serif;color:var(--white)}
.ad{
  position:absolute;left:0;top:447px;width:1200px;height:1697px;overflow:hidden;
  background:
    radial-gradient(ellipse 700px 600px at 110% -5%, rgba(140,30,90,.75), transparent 70%),
    radial-gradient(ellipse 700px 500px at -10% 105%, rgba(110,25,80,.6), transparent 70%),
    radial-gradient(ellipse 600px 600px at 70% 45%, rgba(20,110,120,.35), transparent 70%),
    linear-gradient(180deg,var(--navy) 0%,var(--navy-deep) 100%);
}
.abs{position:absolute}
.spec-badge{left:73px;top:94px;width:236px;height:236px;border-radius:50%;background:#f2f2f4;box-shadow:0 0 0 4px rgba(255,255,255,.15)}
.headline{left:347px;top:94px;line-height:62px}
.headline .light{font-weight:300;font-size:48px;letter-spacing:1px;display:block;line-height:62px}
.headline .bold{font-weight:800;font-size:43px;color:var(--cyan);display:block;line-height:54px}
.intro{left:78px;top:364px;font-size:30px;line-height:39px;font-weight:400}
.intro strong{color:var(--red);font-weight:700;display:block}
.art{left:572px;top:461px;width:584px;height:598px;border-radius:24px;
  background:radial-gradient(ellipse at 55% 55%, rgba(60,70,190,.55), rgba(30,150,160,.25) 55%, transparent 75%)}
.experts{left:260px;top:625px;width:180px;height:50px;background:var(--red);border-radius:0 25px 25px 0;
  font-size:25px;font-weight:500;display:flex;align-items:center;justify-content:center}
.label{font-size:25px;line-height:29px;font-weight:400}
.label.center{text-align:center;width:240px}
.ally-badge{left:74px;top:1450px;width:238px;height:114px;border-radius:4px;background:#fff;border-top:22px solid #4a86e8}
.brand{left:399px;top:1470px;display:flex;align-items:center;gap:22px}
.brand-mark{width:90px;height:90px;background:var(--white)}
.brand-name{font-weight:700;font-size:43px;letter-spacing:3px;line-height:46px}
.brand-tag{font-weight:400;font-size:16px;letter-spacing:1px;line-height:22px}
.url{left:78px;top:1612px;font-size:31px;font-weight:600;letter-spacing:.5px}
</style>
</head>
<body>
<main class="ad">
  <svg class="abs" width="1200" height="1697" viewBox="0 0 1200 1697" aria-hidden="true">
    <g fill="none" stroke="var(--cyan)" stroke-width="3">
      <polyline points="260,650 142,650 142,1220 1113,1220"/>
      <line x1="551" y1="1637" x2="1200" y2="1637"/>
    </g>
    <g fill="var(--cyan)">
      <circle cx="142" cy="650" r="6"/><circle cx="142" cy="903" r="6"/>
      <circle cx="367" cy="1220" r="6"/><circle cx="629" cy="1220" r="6"/>
      <circle cx="890" cy="1220" r="6"/><circle cx="1113" cy="1220" r="6"/>
    </g>
    <g id="nodes" fill="#fff" stroke="var(--red)" stroke-width="7">
      <circle cx="142" cy="789" r="60"/><circle cx="142" cy="1017" r="60"/>
      <circle cx="238" cy="1220" r="60"/><circle cx="498" cy="1220" r="60"/>
      <circle cx="760" cy="1220" r="60"/><circle cx="1021" cy="1220" r="60"/>
    </g>
    <g fill="none" stroke="#2b3a6b" stroke-width="2.5" stroke-linejoin="round">
      <path d="M128,778 a10,10 0 0 1 10,-12 a12,12 0 0 1 22,4 a8,8 0 0 1 0,16 h-30 a8,8 0 0 1 -2,-8z"/>
      <path d="M142,786 v10 M124,796 h36 M124,796 v8 M160,796 v8"/><rect x="116" y="804" width="16" height="12"/><rect x="152" y="804" width="16" height="12"/>
      <rect x="118" y="1001" width="48" height="30"/><path d="M112,1035 h60 M128,1008 v16 M136,1008 v16 M148,1008 h10 M148,1016 h10"/>
      <rect x="216" y="1198" width="44" height="32"/><path d="M208,1236 h60 M226,1214 l12,-10 l12,10 M238,1204 v18"/>
      <circle cx="494" cy="1228" r="14"/><circle cx="494" cy="1228" r="5"/><path d="M490,1200 h24 l-8,12 M516,1196 a4,4 0 1 1 0.1,0"/>
      <rect x="746" y="1194" width="28" height="48" rx="3"/><path d="M752,1214 a5,5 0 0 1 8,-4 a6,6 0 0 1 10,4 z M756,1234 h8"/>
      <rect x="999" y="1196" width="44" height="32"/><path d="M1021,1228 v14 M1009,1242 h24 M1021,1212 a6,6 0 1 1 0.1,0"/>
    </g>
  </svg>

  <div class="abs spec-badge" role="img" aria-label="Task Renewal Mastery badge"></div>

  <h1 class="abs headline">
    <span class="light">FIRST SPANISH CONSULTING</span>
    <span class="light">COMPANY SPECIALIZED IN</span>
    <span class="bold">CLOUD COMPUTING TECHNOLOGY</span>
    <span class="bold">AND SERVICES</span>
  </h1>

  <p class="abs intro">We help you incorporate into your business the<br>best Cloud Computing Solutions on the market<strong>to improve efficiency, reduce costs and<br>increase competitiveness</strong></p>

  <div class="abs art" role="img" aria-label="Isometric illustration of a consultant beside a smartphone with a password dialog, a cloud and glowing data blocks"></div>

  <div class="abs experts">Experts in:</div>

  <p class="abs label" style="left:253px;top:754px">Cloud infrastructure<br>modernization</p>
  <p class="abs label" style="left:253px;top:981px">Digital Transformation,<br>productivity and<br>collaboration</p>
  <p class="abs label center" style="left:118px;top:1299px">Cloud data<br>management</p>
  <p class="abs label center" style="left:378px;top:1299px">Advanced<br>analytics</p>
  <p class="abs label center" style="left:640px;top:1299px">Cloud application<br>development</p>
  <p class="abs label center" style="left:901px;top:1299px">Location Strategy</p>

  <div class="abs ally-badge" role="img" aria-label="Norvane Sky Ally Prime badge"></div>

  <div class="abs brand">
    <span class="brand-mark"></span>
    <div>
      <div class="brand-name">BREVOLTA<br>PARTNER</div>
      <div class="brand-tag">THE CLOUD CONSULTING COMPANY</div>
    </div>
  </div>

  <p class="abs url">www.brevoltaconsult.example</p>
</main>
</body>
</html>
```